Business Card Design for sports performance / psychology company

You can see my website that this is based upon here:
http://www.trelvanedge.co.uk

More than happy to answer any additional questions that you might have

** Happy for any images from Pixelvault to be used. If I go with your design I will purchase the image for you to use

Target Market(s)

Football players

Industry/Entity Type

Business

Contact Information for Business Card

Name: Clive Arnott
Title: Clinical Hypnotherapist & Strategist
Email address: clive@trelvanedge.co.uk
Tel: 07912486015

Font styles to use
Other font styles liked:
• Same font as on website. I'm not actually sure what it is

Requirements
Must have
• Tagline:
• Focus x Drive = Results
• Don't put form down to chance
Nice to have
• Happy for designers to be creative
Should not have

```html
<!DOCTYPE html>
<html lang="en">
<head>
<meta charset="utf-8">
<title>Trelvan Edge – Business Cards</title>
<link rel="stylesheet" href="https://fonts.googleapis.com/css2?family=Jost:wght@400&family=Lato:wght@300;400;700&display=swap">
<style>
  :root {
    --backdrop: #222222;
    --card: #ffffff;
    --navy: #211c45;
    --ink: #333333;
    --band-grey: #333333;
    --rule: #444444;
  }
  * { margin: 0; padding: 0; box-sizing: border-box; }
  html, body {
    width: 1189px; height: 1200px; overflow: hidden;
    background: var(--backdrop);
    font-family: "Lato", sans-serif;
  }
  .canvas { position: relative; width: 1189px; height: 1200px; }
  .card {
    position: absolute; left: 171px; width: 855px; height: 488px;
    background: var(--card); border-radius: 26px; overflow: hidden;
  }
  .card--front { top: 67px; }
  .card--back { top: 626px; }

  .brand-mark { position: absolute; background: var(--navy); }
  .brand-name {
    position: absolute; font-family: "Jost", sans-serif; font-weight: 400;
    color: var(--navy); white-space: nowrap; line-height: 1;
  }

  .card--front .brand-mark { left: 386px; top: 141px; width: 84px; height: 84px; }
  .card--front .brand-name {
    left: 0; width: 855px; text-align: center; top: 243px;
    font-size: 72px; letter-spacing: 4px;
  }
  .tagline {
    position: absolute; left: 0; width: 855px; text-align: center; top: 322px;
    font-size: 24px; line-height: 28px; color: var(--ink); font-weight: 400;
  }

  .card--back .brand-mark { left: 38px; top: 60px; width: 96px; height: 96px; }
  .card--back .brand-name { left: 170px; top: 83px; font-size: 52px; letter-spacing: 2px; }

  .person { position: absolute; right: 40px; top: 248px; text-align: right; color: var(--navy); }
  .person__name { font-size: 33px; line-height: 40px; }
  .person__name strong { font-weight: 700; }
  .person__name span { font-weight: 400; }
  .person__title { font-size: 23px; font-weight: 300; color: var(--ink); line-height: 30px; }

  .rule { position: absolute; left: 38px; width: 777px; top: 322px; border-top: 1.5px solid var(--rule); }

  .contacts { position: absolute; left: 38px; top: 356px; list-style: none; }
  .contacts li {
    display: flex; align-items: center; gap: 11px;
    font-size: 24px; font-weight: 300; color: var(--ink); height: 28px;
  }
  .contacts svg { width: 23px; height: 23px; flex: none; }
  .contacts .web-domain { color: var(--navy); font-weight: 400; }

  .address {
    position: absolute; right: 40px; top: 349px; text-align: right;
    font-size: 24px; font-weight: 300; color: var(--ink); line-height: 28px; font-style: normal;
  }

  .footer-band { position: absolute; left: 0; top: 0; width: 855px; height: 488px; pointer-events: none; }
</style>
</head>
<body>
<main class="canvas">

  <section class="card card--front" aria-label="Card front">
    <div class="brand-mark" aria-hidden="true"></div>
    <h1 class="brand-name">TRELVAN EDGE</h1>
    <p class="tagline">Focus x Drive = Results</p>
  </section>

  <section class="card card--back" aria-label="Card back">
    <div class="brand-mark" aria-hidden="true"></div>
    <h2 class="brand-name">TRELVAN EDGE</h2>

    <div class="person">
      <p class="person__name"><strong>Clive</strong> <span>Arnott</span></p>
      <p class="person__title">Clinical Hypnotherapist &amp; Strategist</p>
    </div>

    <div class="rule"></div>

    <ul class="contacts">
      <li>
        <svg viewBox="0 0 24 24" aria-hidden="true"><rect width="24" height="24" rx="3" fill="var(--navy)"/><path d="M5 9c2-3 12-3 14 0l-2 2-2-1V8H9v2l-2 1z M7 12h10l1 6H6z" fill="#fff"/></svg>
        07912486015
      </li>
      <li>
        <svg viewBox="0 0 24 24" aria-hidden="true"><rect x="1.5" y="4.5" width="21" height="15" fill="none" stroke="var(--navy)" stroke-width="2"/><path d="M2 5l10 8 10-8M2 19l7-7M22 19l-7-7" fill="none" stroke="var(--navy)" stroke-width="1.6"/></svg>
        clive@trelvanedge.co.uk
      </li>
      <li>
        <svg viewBox="0 0 24 24" aria-hidden="true"><rect width="24" height="24" rx="3" fill="var(--navy)"/><circle cx="12" cy="12" r="7.5" fill="none" stroke="#fff" stroke-width="1.4"/><ellipse cx="12" cy="12" rx="3.2" ry="7.5" fill="none" stroke="#fff" stroke-width="1.2"/><path d="M4.5 12h15M6 8h12M6 16h12" stroke="#fff" stroke-width="1.2"/></svg>
        <span>www.<span class="web-domain">trelvanedge</span>.co.uk</span>
      </li>
    </ul>

    <address class="address">
      Tamar Innovation Park<br>
      Tamar &amp; Beaufort Street<br>
      London
    </address>

    <svg class="footer-band" viewBox="0 0 855 488" aria-hidden="true">
      <polygon points="0,463 484,463 477,488 0,488" fill="var(--band-grey)"/>
      <polygon points="499,449 855,449 855,488 486,488" fill="var(--navy)"/>
    </svg>
  </section>

</main>
</body>
</html>
```